Website for a Psychologist in Private Practice

I need a cool web design for my website: www.drkalvoric.com. I would like it to look professional. Keep all the current content and add: Space for video; radio spots (see Silver Cedar Tunes Logo below for those); Quick Inquiry; Friendora link; 5 star rating on Rivo; a map; reviews from former patients. I am open to suggestions.

Target Market(s)

Those seeking individual and marital counseling.

Industry/Entity Type

Mental Health

Number of Pages Required

1 page

Font styles to use
Sans Serif
Other font styles liked:
• I'm open but no hard to read script

Requirements
Must have
• All the content on my home page with link for video and radio spots. List services and degrees and expertices (pics not necessary).
Nice to have
• A video of me and radio conversations (logo of Silver Cedar Tunes radio attached).
Should not have
• Cartoons, comedy, etc.... I don't need pictures of services (marital, depression, etc...) Just list those.

```html
<!DOCTYPE html>
<html lang="en">
<head>
<meta charset="utf-8">
<title>Dr. Marla J. Kalvoric – Psychologist</title>
<link href="https://fonts.googleapis.com/css2?family=Cinzel:wght@400;700&family=Lato:ital,wght@0,400;0,700;0,900;1,400&display=swap" rel="stylesheet">
<style>
:root{
  --blue:#1f7fc4;
  --blue-dark:#1767a3;
  --green:#0f9a12;
  --green-dark:#0b7d0e;
  --ink:#1f1f1f;
  --text:#333;
  --grey-bg:#f3f3f3;
  --rule:#cfcfcf;
  --footer:#3a8cc8;
  --bottom:#5d5d5d;
  --white:#fff;
}
*{box-sizing:border-box;margin:0;padding:0}
html,body{width:904px;height:1200px;overflow:hidden}
body{position:relative;background:var(--white);font-family:'Lato',sans-serif;color:var(--text)}
.abs{position:absolute}

.topline{left:0;top:0;width:904px;height:2px;background:var(--blue)}
.brand{left:58px;top:14px;font-family:'Cinzel',serif;font-size:32px;color:var(--blue);letter-spacing:.5px}
.schedule{left:656px;top:0;width:206px;height:27px;background:var(--blue);clip-path:polygon(0 0,100% 0,94% 100%,6% 100%);color:var(--white);font-size:12px;font-weight:700;display:flex;align-items:center;justify-content:center;gap:7px}
.contact-top{top:42px;display:flex;align-items:center;gap:7px;font-size:12.5px;color:#333}
.dot{width:20px;height:20px;border-radius:50%;background:var(--green);display:flex;align-items:center;justify-content:center}

.nav{left:0;top:72px;width:904px;height:33px;background:var(--green);display:flex;font-family:'Cinzel',serif;font-size:12.5px;color:var(--white);padding-left:60px}
.nav a{color:inherit;text-decoration:none;display:flex;align-items:center;justify-content:center;border-right:1px solid rgba(255,255,255,.25);letter-spacing:.6px}
.nav a.active{background:var(--blue)}
.nav a:last-child{border-right:none}

.hero{left:0;top:105px;width:904px;height:346px;background:linear-gradient(100deg,#c9c4bd 0%,#e6e3dd 35%,#f1efea 55%,#d8d6d2 75%,#a6a19b 100%)}
.hero-title{left:0;top:350px;width:904px;text-align:center;font-family:'Cinzel',serif;font-size:26px;color:var(--ink);letter-spacing:.5px}
.arrow-hero{top:265px}

.service{top:404px;width:120px;text-align:center}
.ring{width:96px;height:96px;border-radius:50%;background:var(--white);border:4px solid var(--green);margin:0 auto;display:flex;align-items:center;justify-content:center;box-shadow:0 2px 6px rgba(0,0,0,.15)}
.ring span{width:62px;height:62px;border-radius:50%;background:radial-gradient(circle,#5fb85f,#138d16)}
.service p{margin-top:8px;font-weight:700;font-size:14px;line-height:18px;color:var(--ink)}

.about-band{left:0;top:575px;width:904px;height:265px;background:var(--grey-bg)}
.h2{font-family:'Cinzel',serif;color:var(--blue);font-size:21px;letter-spacing:.3px;white-space:nowrap}
.h2.small{font-size:17.5px;letter-spacing:.2px;top:865px}
.rule{height:1px;background:var(--rule)}
.para{font-size:11px;line-height:18px;color:var(--ink)}
.degrees-label{left:62px;top:742px;font-family:'Cinzel',serif;font-size:18px;color:var(--ink)}
.ticks{list-style:none;font-size:11px;color:var(--ink)}
.ticks li{height:21px;display:flex;align-items:center;gap:6px}
.video{left:584px;top:647px;width:259px;height:133px;background:linear-gradient(90deg,#c8c0b6,#e3ddd5 45%,#cfc3b4 75%,#b9ab9b)}
.video-bar{left:584px;top:780px;width:259px;height:22px;background:#1b1b1b;display:flex;align-items:center;padding:0 8px;gap:8px}
.track{flex:1;height:4px;background:#555;border-radius:2px;position:relative}
.track i{position:absolute;left:0;top:0;width:34%;height:4px;background:#d32020;border-radius:2px}

.sessions{font-size:10.5px;color:var(--ink)}
.sessions li{list-style:none;height:25.5px;display:flex;align-items:center;gap:4px}
.btn{background:var(--green);color:var(--white);font-size:10px;font-weight:900;letter-spacing:.5px;display:flex;align-items:center;justify-content:center}
.field{left:367px;width:195px;border:1px solid #999;background:var(--white);font-size:10.5px;color:#222;padding:6px 8px}
.quote{left:598px;top:920px;width:245px;height:100px;border:1px solid #d5d5d5;border-radius:6px;background:var(--white);padding:14px 10px;font-style:italic;font-size:10px;line-height:17.5px;color:var(--ink)}

.footer{left:0;top:1080px;width:904px;height:89px;background:var(--footer)}
.fnav{top:1097px;font-size:11px;color:var(--white)}
.fline{left:60px;top:1125px;width:570px;height:1px;background:rgba(255,255,255,.35)}
.fcontact{top:1137px;font-size:12px;color:var(--white);display:flex;align-items:center;gap:6px}
.badge{top:1118px;width:76px;height:34px;background:var(--white)}
.bottom{left:0;top:1169px;width:904px;height:31px;background:var(--bottom)}
.social{top:1173px;height:22px;display:flex;align-items:center;gap:5px;font-size:10px;color:var(--white)}
.social b{width:10px;height:10px;border:1px solid #ddd;border-radius:50%}
</style>
</head>
<body>

<div class="abs topline"></div>
<div class="abs brand">Dr. Marla J. Kalvoric</div>
<div class="abs schedule">
  <svg width="16" height="16" viewBox="0 0 16 16"><rect x="1" y="3" width="12" height="11" fill="none" stroke="#fff" stroke-width="1.4"/><line x1="1" y1="6" x2="13" y2="6" stroke="#fff" stroke-width="1.4"/><circle cx="12" cy="12" r="3.5" fill="#1f7fc4" stroke="#fff" stroke-width="1.2"/></svg>
  Schedule An Appointment
</div>
<div class="abs contact-top" style="left:580px">
  <span class="dot"><svg width="10" height="8" viewBox="0 0 10 8"><rect x=".5" y=".5" width="9" height="7" fill="none" stroke="#fff"/><path d="M.5 .5 5 4.5 9.5 .5" fill="none" stroke="#fff"/></svg></span>
  mk@drkalvoric.com
</div>
<div class="abs contact-top" style="left:727px">
  <span class="dot"><svg width="10" height="10" viewBox="0 0 10 10"><path d="M2 1 4 3 3 4.5Q4.5 6.5 5.5 7L7 6 9 8 7.5 9.5Q3 9 .5 2.5Z" fill="#fff"/></svg></span>
  <span style="font-size:13.5px">(555) 014 2290</span>
</div>

<nav class="abs nav">
  <a class="active" style="width:71px">Home</a>
  <a style="width:107px">Bio</a>
  <a style="width:177px">My Expertise</a>
  <a style="width:143px">Sessions</a>
  <a style="width:159px">Resources</a>
  <a style="width:187px">Contact Me</a>
</nav>

<div class="abs hero" role="img" aria-label="Photo of a couple on a sofa talking with a counselor"></div>
<svg class="abs arrow-hero" style="left:22px" width="14" height="40" viewBox="0 0 14 40"><path d="M12 2 2 20 12 38" fill="none" stroke="rgba(255,255,255,.6)" stroke-width="2"/></svg>
<svg class="abs arrow-hero" style="left:866px" width="14" height="40" viewBox="0 0 14 40"><path d="M2 2 12 20 2 38" fill="none" stroke="rgba(255,255,255,.6)" stroke-width="2"/></svg>
<div class="abs hero-title">Helping You To &nbsp;Find Your Own Solutions</div>

<div class="abs service" style="left:49px"><div class="ring"><span role="img" aria-label="Dating icon"></span></div><p>Dating</p></div>
<div class="abs service" style="left:185px"><div class="ring"><span role="img" aria-label="Marriage icon"></span></div><p>Marriage</p></div>
<div class="abs service" style="left:322px"><div class="ring"><span role="img" aria-label="Professional relationship icon"></span></div><p>Professional<br>Relationship</p></div>
<div class="abs service" style="left:458px"><div class="ring"><span role="img" aria-label="Depression and anxiety icon"></span></div><p>Depression &amp;<br>Anxiety Issues</p></div>
<div class="abs service" style="left:593px"><div class="ring"><span role="img" aria-label="Personality disorders icon"></span></div><p>Personality<br>Disorders</p></div>
<div class="abs service" style="left:730px"><div class="ring"><span role="img" aria-label="Life management icon"></span></div><p>Life<br>Management</p></div>

<section class="abs about-band"></section>
<h2 class="abs h2" style="left:60px;top:597px">About Dr. Marla J. Kalvoric</h2>
<div class="abs rule" style="left:60px;top:632px;width:481px"></div>
<p class="abs para" style="left:62px;top:642px;width:485px">Lorem ipsum dolor sit amet, consectetuer adipiscing elit, sed diam nonummy nibh euismod tincidunt ut laoreet dolore magna aliquam erat volutpat. Ut wisi enim ad minim veniam, quis nostrud exerci tation ullamcorper suscipit lobortis nisl ut aliquip ex ea commodo consequat.</p>
<div class="abs degrees-label">My Degrees</div>
<svg class="abs" style="left:172px;top:710px" width="30" height="90" viewBox="0 0 30 90"><path d="M6 2Q18 2 18 16V36Q18 44 26 45Q18 46 18 54V74Q18 88 6 88" fill="none" stroke="#1f1f1f" stroke-width="4"/></svg>
<ul class="abs ticks" style="left:210px;top:713px">
  <li><svg width="11" height="9" viewBox="0 0 11 9"><path d="M1 5 4 8 10 1" fill="none" stroke="#0f9a12" stroke-width="2"/></svg>Doctoral Degree in Clinical Psychology</li>
  <li><svg width="11" height="9" viewBox="0 0 11 9"><path d="M1 5 4 8 10 1" fill="none" stroke="#0f9a12" stroke-width="2"/></svg>Masters Degree in Counseling Psychology</li>
  <li><svg width="11" height="9" viewBox="0 0 11 9"><path d="M1 5 4 8 10 1" fill="none" stroke="#0f9a12" stroke-width="2"/></svg>Doctoral Internship, Bayside Medical Center</li>
  <li><svg width="11" height="9" viewBox="0 0 11 9"><path d="M1 5 4 8 10 1" fill="none" stroke="#0f9a12" stroke-width="2"/></svg>Masters Internship, Westbrook Clinic</li>
</ul>
<div class="abs" style="left:563px;top:625px;width:1px;height:185px;background:#e2e2e2"></div>
<h2 class="abs h2" style="left:583px;top:597px">View Video</h2>
<div class="abs rule" style="left:583px;top:633px;width:260px"></div>
<div class="abs video" role="img" aria-label="Video still of a counseling session"></div>
<div class="abs video-bar">
  <svg width="9" height="10" viewBox="0 0 9 10"><path d="M1 1 8 5 1 9Z" fill="#fff"/></svg>
  <svg width="11" height="10" viewBox="0 0 11 10"><path d="M1 3H3L6 1V9L3 7H1Z" fill="#ccc"/><path d="M8 3Q9.5 5 8 7" stroke="#ccc" fill="none"/></svg>
  <div class="track"><i></i></div>
  <svg width="10" height="10" viewBox="0 0 10 10"><path d="M6 1H9V4M4 9H1V6M9 1 5.5 4.5M1 9 4.5 5.5" stroke="#ccc" fill="none" stroke-width="1.3"/></svg>
</div>

<h2 class="abs h2 small" style="left:60px">My Sessions</h2>
<div class="abs rule" style="left:60px;top:896px;width:249px"></div>
<ul class="abs sessions" style="left:60px;top:911px">
  <li><svg width="10" height="9" viewBox="0 0 11 9"><path d="M1 5 4 8 10 1" fill="none" stroke="#111" stroke-width="2"/></svg>Individual Sessions</li>
  <li><svg width="10" height="9" viewBox="0 0 11 9"><path d="M1 5 4 8 10 1" fill="none" stroke="#111" stroke-width="2"/></svg>Marriage Sessions</li>
  <li><svg width="10" height="9" viewBox="0 0 11 9"><path d="M1 5 4 8 10 1" fill="none" stroke="#111" stroke-width="2"/></svg>Family Sessions</li>
  <li><svg width="10" height="9" viewBox="0 0 11 9"><path d="M1 5 4 8 10 1" fill="none" stroke="#111" stroke-width="2"/></svg>Phone Sessions</li>
</ul>
<ul class="abs sessions" style="left:168px;top:911px">
  <li><svg width="10" height="9" viewBox="0 0 11 9"><path d="M1 5 4 8 10 1" fill="none" stroke="#111" stroke-width="2"/></svg>Divorce Mediation</li>
  <li><svg width="10" height="9" viewBox="0 0 11 9"><path d="M1 5 4 8 10 1" fill="none" stroke="#111" stroke-width="2"/></svg>Custody Evaluation Sessions</li>
  <li><svg width="10" height="9" viewBox="0 0 11 9"><path d="M1 5 4 8 10 1" fill="none" stroke="#111" stroke-width="2"/></svg>Testing Sessions</li>
  <li><svg width="10" height="9" viewBox="0 0 11 9"><path d="M1 5 4 8 10 1" fill="none" stroke="#111" stroke-width="2"/></svg>Weekend / Holiday Sessions</li>
</ul>
<div class="abs btn" style="left:60px;top:1027px;width:75px;height:23px">READ MORE</div>

<h2 class="abs h2 small" style="left:366px">Quick Inquiry</h2>
<div class="abs rule" style="left:366px;top:896px;width:197px"></div>
<div class="abs field" style="top:918px;height:23px">Name</div>
<div class="abs field" style="top:948px;height:23px">Email</div>
<div class="abs field" style="top:978px;height:40px">Message</div>
<div class="abs btn" style="left:367px;top:1025px;width:67px;height:23px">SUBMIT</div>

<h2 class="abs h2 small" style="left:595px">Radio Conversations</h2>
<svg class="abs" style="left:817px;top:870px" width="28" height="12" viewBox="0 0 28 12"><path d="M5 1 1 6 5 11M22 1 26 6 22 11" fill="none" stroke="#222" stroke-width="2"/></svg>
<div class="abs rule" style="left:595px;top:896px;width:248px"></div>
<div class="abs quote">Lorem ipsum dolor sit amet, consectetuer adipiscingelit, sed diam nonummy nibh euismod tinciduntttfgf dolore magna aliquam erat volutpat. tinciduntpsum dolor sit amet, consectetuer adip</div>
<svg class="abs" style="left:690px;top:1019px" width="34" height="18" viewBox="0 0 34 18"><path d="M0 1H30L32 16Z" fill="#fff"/><path d="M0 1 32 16 30 1" fill="none" stroke="#d5d5d5"/></svg>
<div class="abs" style="left:700px;top:1025px;width:143px;text-align:right;font-size:10.5px;font-weight:700;color:var(--ink)">- Lorem ipsum dolor</div>
<div class="abs" style="left:760px;top:1039px;font-size:9px;font-style:italic;color:var(--blue)">Sitamet, CA</div>

<footer class="abs footer"></footer>
<div class="abs fnav" style="left:62px">Home</div>
<div class="abs fnav" style="left:133px">Bio</div>
<div class="abs fnav" style="left:191px">My Expertise</div>
<div class="abs fnav" style="left:304px">Sessions</div>
<div class="abs fnav" style="left:393px">Resources</div>
<div class="abs fnav" style="left:493px">Contact Me</div>
<div class="abs fline"></div>
<div class="abs fcontact" style="left:62px"><svg width="9" height="10" viewBox="0 0 10 10"><path d="M2 1 4 3 3 4.5Q4.5 6.5 5.5 7L7 6 9 8 7.5 9.5Q3 9 .5 2.5Z" fill="#fff"/></svg>(555) 014 2290</div>
<div class="abs fcontact" style="left:189px"><svg width="11" height="8" viewBox="0 0 10 8"><rect x=".5" y=".5" width="9" height="7" fill="none" stroke="#fff"/><path d="M.5 .5 5 4.5 9.5 .5" fill="none" stroke="#fff"/></svg>mk@drkalvoric.com</div>
<div class="abs fcontact" style="left:343px"><svg width="8" height="11" viewBox="0 0 8 11"><path d="M4 11Q0 5 0 4A4 4 0 0 1 8 4Q8 5 4 11Z" fill="#fff"/><circle cx="4" cy="4" r="1.5" fill="#3a8cc8"/></svg>418 Linden Way, Suite 120 &nbsp;Harbor Vale, CA 90412</div>
<div class="abs" style="left:640px;top:1097px;width:203px;text-align:right;font-size:11px;font-weight:700;color:var(--white)">A portion of all revenue is donated to</div>
<div class="abs badge" style="left:683px" role="img" aria-label="Partner charity badge"></div>
<div class="abs badge" style="left:767px" role="img" aria-label="Partner charity badge"></div>

<div class="abs bottom"></div>
<div class="abs" style="left:62px;top:1177px;font-size:10.5px;color:#eee">Copyright © 2016 Dr. Marla J. Kalvoric. All Rights Reserved.</div>
<div class="abs social" style="left:735px"><b></b>Friendora</div>
<div class="abs social" style="left:797px"><b></b>Chirpline</div>

</body>
</html>
```